BRANDEMEIER & BRANDEMEIER,LLP NEEDS A NEW LETTERHEAD DESIGN

a conservative yet contemporary layout befitting a long established
firm, consistent with the times, some form of logo so it catches ones attention, and is
admirable, but portrays integrity
Updates

I would like to approve #22066987 Please advise how to do this as it’s confusing on the site so I can approve payment for the designer

Target Market(s)

real estate investors and building management people

Industry/Entity Type

Law Firm

Font styles to use
Serif

Colors

Designer to choose colors to be used in the design.

Requirements
Must have
• some form of conservative logo

```html
<!DOCTYPE html>
<html lang="en">
<head>
<meta charset="utf-8">
<title>Brandemeier &amp; Brandemeier, LLP — Letterhead</title>
<link rel="stylesheet" href="https://fonts.googleapis.com/css2?family=EB+Garamond:wght@400;500&family=Open+Sans:wght@400;700&family=Arimo&display=swap">
<style>
  :root {
    --backdrop: #dfe2e4;
    --paper: #ffffff;
    --ink-dark: #3a4550;
    --ink-body: #6e6e6e;
    --ink-soft: #8a8f95;
    --accent: #6f8799;
    --rule: #c9cdd1;
  }
  * { margin: 0; padding: 0; box-sizing: border-box; }
  html, body { width: 1200px; height: 784px; overflow: hidden; background: var(--backdrop); }
  .letterhead {
    position: absolute; left: 337px; top: 20px; width: 526px; height: 744px;
    background: var(--paper);
    box-shadow: 0 2px 10px rgba(0,0,0,0.12);
  }
  .top-band { position: absolute; left: 0; top: 0; width: 100%; height: 6px; background: var(--ink-dark); }
  .firm-name {
    position: absolute; left: 40px; top: 40px;
    font-family: "EB Garamond", serif; font-weight: 500; font-size: 19px; line-height: 1.1;
    color: var(--ink-dark); letter-spacing: 0.5px;
    display: flex; align-items: center; gap: 10px;
  }
  .firm-mark { width: 12px; height: 12px; background: var(--ink-dark); flex: none; }
  .contact {
    position: absolute; right: 34px; top: 36px; width: 150px;
    border-left: 1px solid var(--rule); padding-left: 10px;
    font-family: "Open Sans", sans-serif; font-size: 7.5px; line-height: 1.55; color: var(--ink-soft);
  }
  .contact li { list-style: none; display: flex; gap: 5px; align-items: flex-start; }
  .contact .address { color: var(--ink-dark); font-weight: 700; }
  .contact svg { width: 8px; height: 8px; flex: none; margin-top: 2px; }
  .body-copy {
    position: absolute; left: 62px; top: 128px; width: 400px;
    font-family: Arimo, Arial, sans-serif; font-size: 10px; line-height: 1.45; color: var(--ink-body);
  }
  .body-copy p { margin-bottom: 12px; }
  .signature {
    position: absolute; left: 62px; top: 545px; width: 150px; height: 42px;
    background: linear-gradient(90deg, #f3f3f3, #ebebeb);
    border-radius: 3px;
  }
  .practice-line {
    position: absolute; left: 40px; bottom: 34px;
    font-family: "EB Garamond", serif; font-size: 14px; color: var(--accent); letter-spacing: 0.3px;
  }
</style>
</head>
<body>
  <main class="letterhead">
    <div class="top-band"></div>

    <header class="firm-name">
      <span class="firm-mark"></span>
      <span>BRANDEMEIER &amp;<br>BRANDEMEIER, LLP</span>
    </header>

    <ul class="contact">
      <li class="address">
        <svg viewBox="0 0 10 10"><circle cx="5" cy="5" r="5" fill="#3a4550"/><path d="M5 2.2a1.8 1.8 0 0 1 1.8 1.8C6.8 5.4 5 7.8 5 7.8S3.2 5.4 3.2 4A1.8 1.8 0 0 1 5 2.2z" fill="#fff"/></svg>
        <span>410 Harbor Street Suite 210<br>Brooklyn, New York 11201</span>
      </li>
      <li>
        <svg viewBox="0 0 10 10"><circle cx="5" cy="5" r="5" fill="#3a4550"/><path d="M3.3 2.6l1 1-.6.7c.3.7.9 1.3 1.6 1.6l.7-.6 1 1-.6.9C4.8 7 3 5.2 2.8 3.2z" fill="#fff"/></svg>
        <span>(555) 014-2287</span>
      </li>
      <li>
        <svg viewBox="0 0 10 10"><circle cx="5" cy="5" r="5" fill="#3a4550"/><rect x="2.8" y="3" width="4.4" height="4" fill="#fff"/></svg>
        <span>(555) 014-3391</span>
      </li>
      <li>
        <svg viewBox="0 0 10 10"><circle cx="5" cy="5" r="5" fill="#3a4550"/><rect x="2.6" y="3.3" width="4.8" height="3.4" fill="#fff"/></svg>
        <span>info@brandemeierlaw.com</span>
      </li>
      <li>
        <svg viewBox="0 0 10 10"><circle cx="5" cy="5" r="5" fill="#8a8f95"/></svg>
        <span>www.brandemeierlaw.com</span>
      </li>
    </ul>

    <section class="body-copy">
      <p>Lorem Ipsum is simply dummy text of the printing and typesetting industry. Lorem Ipsum has been the industry's standard dummy text ever since the 1500s, when an unknown printer took a galley of type and scrambled it to make a type specimen book. It has survived not only five centuries, but also the leap into electronic typesetting, remaining essentially unchanged. It was popularised in the 1960s with the release of Typeline sheets containing Lorem Ipsum passages, and more recently with desktop publishing software like PageCraft Studio including versions of Lorem Ipsum.</p>
      <p>It is a long established fact that a reader will be distracted by the readable content of a page when looking at its layout. The point of using Lorem Ipsum is that it has a more-or-less normal distribution of letters, as opposed to using 'Content here, content here', making it look like readable English. Many desktop publishing packages and web page editors now use Lorem Ipsum as their default model text, and a search for 'lorem ipsum' will uncover many web sites still in their infancy. Various versions have evolved over the years, sometimes by accident, sometimes on purpose (injected humour and the like).</p>
      <p>Contrary to popular belief, Lorem Ipsum is not simply random text. It has roots in a piece of classical Latin literature from 45 BC, making it over 2000 years old. A Latin professor at a college in Virginia looked up one of the more obscure Latin words, consectetur, from a Lorem Ipsum passage, and going through the cites of the word in classical literature, discovered the undoubtable source. Lorem Ipsum comes from sections 1.10.32 and 1.10.33 of "de Finibus Bonorum et Malorum" structures, to generate Lorem Ipsum which looks reasonable. The generated Lorem Ipsum is therefore always free from repetition, injected humour, or non-characteristic words etc.</p>
    </section>

    <div class="signature" role="img" aria-label="Handwritten signature"></div>

    <footer class="practice-line">New York City Landlord / Tenant Real Estate Law</footer>
  </main>
</body>
</html>
```